AUTOMOTIVE/ CAR REPAIRS / CRASH REPAIRS / PAINT SPRAYING AND PANEL BEATING

AUTOMOTIVE REPAIR. CAR / MOTORCYCLES GOT LOGO DESIGN / DID THINK ABOUT FACEBOOK DONT NOALREADY HAVE WEB ADRESS www.brenvashine.co.uk and mail sales@brenvashine,co.uk NEED SOMETHINK I CAN MANAGE TO UPLOAD PICTURES IN TO A GALLERY OR SOMETHINGLIKE THAT I ALSO SELL CAR AND MOTORCYCLES MAYBE A SELLS PAGE WITH A TILLWAVE LINK

Target Market(s)

TRADE / GENERAL PUBLIC

Industry/Entity Type

Automotive

Coding

Coded - Design and coding required

Number of Pages Required

4 page

Font styles to use
Serif
Sans Serif

Colors

Designer to choose colors to be used in the design.

Requirements
Must have
• GALLERY/ SHOP TO SALE CARS AND MOTORCYCLE / LOGOS OF MATERIALS I USE DORFLINT / KEBO / VASTINCO / Q WRAP / GLENBRUSH
• CONTACT US
Nice to have
• TILLWAVE / EASY TO MANAGE / VIDEO CLIP OF DORFLINT HUE PLANNER Z7
• SWIFT BLEND PAINT TONVIEW WETLINE AND TULVOKE

```html
<!DOCTYPE html>
<html lang="en">
<head>
<meta charset="utf-8">
<title>Brenvashine Bodyshop</title>
<link href="https://fonts.googleapis.com/css2?family=Montserrat:ital,wght@0,400;0,500;0,600;0,700;0,800;1,400;1,700;1,800&display=swap" rel="stylesheet">
<style>
:root{
  --red:#9b1c22;
  --red-bright:#d0202a;
  --ink:#1b1d23;
  --dark:#1d1f25;
  --slate:#2b2e36;
  --grey:#6d6f75;
  --line:#c9cbd0;
  --white:#ffffff;
  --star:#f3a41c;
}
*{box-sizing:border-box;margin:0;padding:0}
html,body{width:1200px;height:4364px;overflow:hidden}
body{position:relative;font-family:"Montserrat",Arial,sans-serif;color:var(--ink);background:var(--white)}
.abs{position:absolute}
.heading{font-weight:800;font-style:italic;font-size:35px;letter-spacing:.5px;text-transform:uppercase}
.center{text-align:center;left:0;width:1200px}
.divider{position:absolute;width:26px;height:4px;background:var(--red-bright);border-radius:2px}
.btn{position:absolute;height:44px;border-radius:22px;background:var(--dark);border:2px solid var(--red-bright);color:var(--white);font-weight:700;font-size:14px;display:flex;align-items:center;justify-content:center;gap:6px;text-transform:uppercase}
.btn svg{width:13px;height:13px}

/* header */
.site-header{left:0;top:0;width:1200px;height:97px;background:var(--ink)}
.brand{left:122px;top:20px;width:240px;color:var(--white);font-weight:800;font-size:26px;letter-spacing:2px;text-align:center}
.brand small{display:block;font-size:10px;font-weight:500;letter-spacing:7px;margin-top:2px}
.topbar{left:390px;top:0;width:810px;height:31px;background:var(--red);color:var(--white);font-size:14px;font-weight:600;display:flex;align-items:center}
.topbar .mail{position:absolute;left:18px;display:flex;align-items:center;gap:10px}
.topbar .call{position:absolute;right:100px;display:flex;align-items:center;gap:12px;font-weight:500}
.topbar .call b{font-size:17px;font-weight:700}
.nav{top:56px;font-size:14.5px;font-weight:600;color:var(--white)}
.nav.active{color:var(--red-bright)}
.nav.active::after{content:"";position:absolute;left:0;right:0;top:24px;height:2px;background:var(--red-bright)}

/* hero */
.hero{left:0;top:97px;width:1200px;height:556px;background:#050505}
.hero-photo{left:560px;top:97px;width:640px;height:556px;background:radial-gradient(ellipse at 60% 45%,#c0141c 0%,#7a0c10 35%,#2a0709 65%,#050505 85%)}
.hero-title{left:112px;top:234px;color:var(--white);font-size:48px;font-weight:800;font-style:italic;letter-spacing:3px}
.hero-text{left:112px;top:296px;width:440px;color:var(--white);font-size:15px;line-height:28px;font-weight:500}
.dots{left:566px;top:563px;display:flex;gap:5px}
.dots i{width:13px;height:13px;border-radius:50%;border:2px solid var(--white)}
.dots i:first-child{background:var(--white)}

/* about */
.about-art{left:17px;top:661px;width:568px;height:585px;background:radial-gradient(circle at 55% 55%,#2b2b2e 0%,#8a8c90 32%,#c4161e 52%,#ffffff 74%)}
.about-title{left:619px;top:748px;line-height:43px}
.about-label{left:619px;top:853px;color:var(--red-bright);font-weight:700;font-size:15px}
.about-text{left:619px;top:888px;width:461px;color:var(--grey);font-size:14px;line-height:28.4px;text-align:justify}

/* services */
.services{left:0;top:1249px;width:1200px;height:1060px;background:linear-gradient(180deg,#2d3039,#24272e)}
.services .heading{color:var(--white)}
.sub-white{color:var(--white);font-size:14.5px;line-height:28px}
.svc-photo{position:absolute;width:310px;height:210px;border:2px solid #e8e8e8}
.svc-card{position:absolute;width:260px;height:187px;background:var(--white);padding:17px 20px 0 20px}
.svc-card.featured{background:var(--red);color:var(--white)}
.svc-card h3{font-size:16.5px;font-weight:700;margin-bottom:6px}
.svc-card p{font-size:13px;line-height:25.5px;color:var(--grey)}
.svc-card.featured p{color:#f1d8d9}
.svc-card .btn{left:20px;top:130px;width:142px;height:40px;font-size:13px}

/* testimonial */
.sub-grey{color:var(--grey);font-size:14.5px;line-height:29px}
.avatar{left:544px;top:2517px;width:112px;height:112px;border-radius:50%;background:linear-gradient(160deg,#d9dbe0,#8b8f98);border:3px solid #e4e5e8}
.stars{top:2648px;color:var(--star);font-size:17px;letter-spacing:3px}
.quote-mark{left:287px;top:2622px;font-size:110px;color:#d4d5d8;font-family:Georgia,serif;font-weight:700;line-height:1}
.quote{left:230px;top:2681px;width:740px;text-align:center;color:var(--grey);font-style:italic;font-size:14px;line-height:29px}
.author{top:2782px;font-weight:700;font-style:italic;font-size:16px}
.arrow{top:2707px;width:46px;height:46px;border-radius:50%;background:#6c6e73;display:flex;align-items:center;justify-content:center}

/* gallery */
.shot{position:absolute}
.shot-overlay{position:absolute;left:0;top:0;right:0;bottom:0;background:rgba(20,22,28,.55);display:flex;align-items:center;justify-content:center;gap:40px;color:var(--white);font-size:15px}
.shot-overlay span{display:flex;align-items:center;gap:6px}

/* partners */
.partner{position:absolute;top:3520px;width:178px;height:82px;display:flex;align-items:center;justify-content:center;font-weight:800;font-size:19px;color:var(--ink);letter-spacing:.5px}
.partner::before,.partner::after{content:"";position:absolute;top:0;bottom:0;width:26px;border:2.5px solid var(--red-bright)}
.partner::before{left:0;border-right:none}
.partner::after{right:0;border-left:none}

/* contact */
.contact-band{left:0;top:3670px;width:1200px;height:407px;background:linear-gradient(90deg,#8c161c,#a51f25)}
.contact-band .heading{color:var(--white)}
.c-item{left:150px;color:var(--white);font-size:15px;line-height:28.5px;display:flex;gap:18px;font-weight:500}
.c-item svg{width:20px;height:20px;flex:none;margin-top:4px}
.footer{left:0;top:4077px;width:1200px;height:287px;background:var(--dark)}
.f-label{left:110px;top:4125px;color:var(--white);font-weight:700;font-size:14px}
.post-thumb{position:absolute;top:4170px;width:78px;height:76px;background:linear-gradient(135deg,#5d5f66,#2a2c32)}
.post{position:absolute;top:4166px;color:var(--white);font-size:12px;line-height:21px}
.post b{font-size:14px}
.post em{color:var(--red-bright);font-style:normal;font-size:12px}
.social{position:absolute;top:4280px;width:54px;height:54px;border-radius:50%;border:2px solid var(--white);color:var(--white);font-size:10px;font-weight:600;display:flex;align-items:center;justify-content:center}
.pay-label{left:739px;top:4294px;color:#b4b6bb;font-size:8px}
.pay-name{left:752px;top:4307px;color:var(--white);font-weight:800;font-size:17px}
.copy{left:862px;top:4307px;color:var(--white);font-size:14px;font-weight:500}

/* appointment */
.appt{left:552px;top:3670px;width:536px;height:613px;background:var(--white);box-shadow:0 4px 20px rgba(0,0,0,.25)}
.appt .heading{position:absolute;left:0;width:536px;top:32px;text-align:center;font-size:33px}
.appt-addr{position:absolute;left:30px;width:476px;top:87px;text-align:center;font-size:14px;line-height:31px;font-weight:500}
.field{position:absolute;left:36px;width:470px;height:42px;border:1.5px solid var(--line);font-size:14px;color:var(--grey);padding-left:18px;display:flex;align-items:center}
.field.select{border-color:#333;color:var(--ink);font-weight:500}
.field.select::after{content:"";position:absolute;right:14px;top:19px;border:5px solid transparent;border-top-color:var(--ink)}
.appt .btn{left:38px;top:439px;width:158px}
.appt-note{position:absolute;left:30px;width:476px;top:498px;text-align:center;font-size:14px;line-height:31px;color:var(--ink)}
</style>
</head>
<body>

<!-- header -->
<header class="abs site-header"></header>
<div class="abs brand">BRENVASHINE<small>BODYSHOP</small></div>
<div class="abs topbar">
  <span class="mail"><svg width="16" height="12" viewBox="0 0 16 12"><rect width="16" height="12" rx="1" fill="#fff"/><path d="M0 1l8 6 8-6" stroke="#9b1c22" stroke-width="1.5" fill="none"/></svg>sales@brenvashine.co.uk</span>
  <span class="call">Call us Today <svg width="15" height="15" viewBox="0 0 24 24"><path fill="#fff" d="M6.6 10.8a15 15 0 006.6 6.6l2.2-2.2c.3-.3.7-.4 1-.2 1.1.4 2.3.6 3.6.6.6 0 1 .4 1 1V20c0 .6-.4 1-1 1A17 17 0 013 4c0-.6.4-1 1-1h3.5c.6 0 1 .4 1 1 0 1.3.2 2.5.6 3.6.1.3 0 .7-.2 1z"/></svg><b>0770 900 1234</b></span>
</div>
<nav>
  <span class="abs nav active" style="left:529px">HOME</span>
  <span class="abs nav" style="left:612px">ABOUT US</span>
  <span class="abs nav" style="left:724px">SERVICE</span>
  <span class="abs nav" style="left:820px">CUSTOM</span>
  <span class="abs nav" style="left:920px">GALLERY</span>
  <span class="abs nav" style="left:1022px">CONTACT</span>
</nav>

<!-- hero -->
<section class="abs hero"></section>
<div class="abs hero-photo" role="img" aria-label="Photo of a glossy red sports car in a dark studio"></div>
<h1 class="abs hero-title">BRENVASHINE</h1>
<p class="abs hero-text">Lorem ipsum dolor sit amet, consectetur adipiscing elit, sed do eiusmod tempor incididunt ut labore</p>
<div class="btn" style="left:112px;top:368px;width:158px">Read more <svg viewBox="0 0 14 14"><circle cx="7" cy="7" r="6" fill="none" stroke="#fff" stroke-width="1.6"/><path d="M5.5 4.5L8 7l-2.5 2.5" stroke="#fff" stroke-width="1.6" fill="none"/></svg></div>
<div class="abs dots"><i></i><i></i><i></i><i></i></div>

<!-- about -->
<div class="abs about-art" role="img" aria-label="Illustration of a black saloon car inside a red and chrome swirl with paint splashes"></div>
<span class="divider" style="left:619px;top:723px"></span>
<h2 class="abs heading about-title">Brenvashine your<br>one stop bodyshop</h2>
<div class="abs about-label">ABOUT US</div>
<p class="abs about-text">Equipped with the latest technology and factory trained technicians, we process accident repairs for all leading insurance and vehicle management companies, specialising in accident repairs for most prestige vehicles manufacturers. We are proud to maintain a close working partnership with several local dealership networks,. Brenvashine aims to continually set new standards of quality control and customer care, by ensuring</p>
<div class="btn" style="left:619px;top:1109px;width:157px">Read more <svg viewBox="0 0 14 14"><circle cx="7" cy="7" r="6" fill="none" stroke="#fff" stroke-width="1.6"/><path d="M5.5 4.5L8 7l-2.5 2.5" stroke="#fff" stroke-width="1.6" fill="none"/></svg></div>

<!-- services -->
<section class="abs services"></section>
<span class="divider" style="left:587px;top:1300px"></span>
<h2 class="abs heading center" style="top:1326px;color:#fff">Our Service</h2>
<p class="abs center sub-white" style="top:1378px;left:280px;width:640px;text-align:center">Lorem ipsum dolor sit amet, consectetur adipiscing elit, sed do eiusmod tempor incididunt ut labore et dolore magna aliqua. Ut enim ad</p>

<div class="svc-photo" style="left:112px;top:1463px;background:linear-gradient(135deg,#c9a38f,#d47c95 55%,#6c5a52)" role="img" aria-label="Photo of a car body in pink primer in a spray booth"></div>
<div class="svc-photo" style="left:444px;top:1463px;background:linear-gradient(135deg,#7b8ab0,#2b3a78 55%,#151b33)" role="img" aria-label="Photo of a blue car panel being polished"></div>
<div class="svc-photo" style="left:776px;top:1463px;background:linear-gradient(135deg,#b5b2ab,#6f6d68 55%,#3a3936)" role="img" aria-label="Photo of a silver saloon with a damaged front bumper"></div>
<div class="svc-card" style="left:137px;top:1632px"><h3>Full or part resprays</h3><p>Sometimes a vehicle would simply benefit from having a complete new coat of paint.</p><div class="btn">Read more <svg viewBox="0 0 14 14"><circle cx="7" cy="7" r="6" fill="none" stroke="#fff" stroke-width="1.6"/><path d="M5.5 4.5L8 7l-2.5 2.5" stroke="#fff" stroke-width="1.6" fill="none"/></svg></div></div>
<div class="svc-card featured" style="left:469px;top:1632px"><h3>Dents &amp; scratch removal</h3><p>The techniques used are methods that enable professionals to repair minor</p><div class="btn">Read more <svg viewBox="0 0 14 14"><circle cx="7" cy="7" r="6" fill="none" stroke="#fff" stroke-width="1.6"/><path d="M5.5 4.5L8 7l-2.5 2.5" stroke="#fff" stroke-width="1.6" fill="none"/></svg></div></div>
<div class="svc-card" style="left:801px;top:1632px"><h3>Bumper repair</h3><p>Car bumper scuff damage can not only harm the appearance of your vehicle</p><div class="btn">Read more <svg viewBox="0 0 14 14"><circle cx="7" cy="7" r="6" fill="none" stroke="#fff" stroke-width="1.6"/><path d="M5.5 4.5L8 7l-2.5 2.5" stroke="#fff" stroke-width="1.6" fill="none"/></svg></div></div>

<div class="svc-photo" style="left:112px;top:1858px;background:linear-gradient(135deg,#8a8984,#d8d2c0 50%,#4b4a47)" role="img" aria-label="Photo of a car wing in filler after an accident"></div>
<div class="svc-photo" style="left:444px;top:1858px;background:radial-gradient(circle,#d8dadd,#8c8f94 50%,#2c2d30)" role="img" aria-label="Photo of a refurbished alloy wheel"></div>
<div class="svc-photo" style="left:776px;top:1858px;background:linear-gradient(135deg,#e8e2df,#c01e2a 45%,#1f2a55)" role="img" aria-label="Photo of a gloved hand polishing a painted panel"></div>
<div class="svc-card" style="left:137px;top:2027px"><h3>Accident repair</h3><p>Sometimes accidents happen which result in you needing your vehicle repairing</p><div class="btn">Read more <svg viewBox="0 0 14 14"><circle cx="7" cy="7" r="6" fill="none" stroke="#fff" stroke-width="1.6"/><path d="M5.5 4.5L8 7l-2.5 2.5" stroke="#fff" stroke-width="1.6" fill="none"/></svg></div></div>
<div class="svc-card" style="left:469px;top:2027px"><h3>Alloy wheel's refurbished</h3><p>The cost of alloy wheel repair or wheel refurbishment is far lower than</p><div class="btn">Read more <svg viewBox="0 0 14 14"><circle cx="7" cy="7" r="6" fill="none" stroke="#fff" stroke-width="1.6"/><path d="M5.5 4.5L8 7l-2.5 2.5" stroke="#fff" stroke-width="1.6" fill="none"/></svg></div></div>
<div class="svc-card" style="left:801px;top:2027px"><h3>Repaired &amp; painted</h3><p>The cost of alloy wheel repair or wheel refurbishment is far lower than</p><div class="btn">Read more <svg viewBox="0 0 14 14"><circle cx="7" cy="7" r="6" fill="none" stroke="#fff" stroke-width="1.6"/><path d="M5.5 4.5L8 7l-2.5 2.5" stroke="#fff" stroke-width="1.6" fill="none"/></svg></div></div>

<!-- testimonial -->
<span class="divider" style="left:587px;top:2366px"></span>
<h2 class="abs heading center" style="top:2390px">What customers said</h2>
<p class="abs sub-grey" style="top:2447px;left:240px;width:720px;text-align:center">Lorem ipsum dolor sit amet, consectetur adipiscing elit, sed do eiusmod tempor incididunt ut labore et dolore magna aliqua. Ut enim ad minim veniam, quis nostrud</p>
<div class="abs avatar" role="img" aria-label="Portrait photo of the reviewing customer"></div>
<div class="abs center stars" style="text-align:center">★★★★★</div>
<div class="abs quote-mark">“</div>
<p class="abs quote">Lorem ipsum dolor sit amet, consectetur adipiscing elit, sed do eiusmod tempor incididunt ut labore et dolore magna aliqua.Ut enim ad minim veniam, quis nostrudLorem ipsum dolor sit amet, consectetur adipiscing elit, sed do eiusmod tempor incididunt ut labore et dolore magna aliqua</p>
<div class="abs center author" style="text-align:center">Tomas Reeve</div>
<div class="abs arrow" style="left:33px"><svg width="14" height="14" viewBox="0 0 14 14"><path d="M9 2L4 7l5 5" stroke="#fff" stroke-width="2" fill="none"/></svg></div>
<div class="abs arrow" style="left:1121px"><svg width="14" height="14" viewBox="0 0 14 14"><path d="M5 2l5 5-5 5" stroke="#fff" stroke-width="2" fill="none"/></svg></div>

<!-- gallery -->
<span class="divider" style="left:587px;top:2864px"></span>
<h2 class="abs heading center" style="top:2888px">Gallery</h2>
<div class="shot" style="left:112px;top:2975px;width:471px;height:215px;background:linear-gradient(160deg,#4a4e57,#15171b)" role="img" aria-label="Photo of a black hatchback in the workshop">
  <div class="shot-overlay"><span><svg width="16" height="14" viewBox="0 0 16 14"><path fill="#fff" d="M8 14L1.3 7.4A4 4 0 018 2a4 4 0 016.7 5.4z"/></svg>8</span><span><svg width="16" height="14" viewBox="0 0 16 14"><path fill="none" stroke="#fff" stroke-width="1.6" d="M2 2h12v8H6l-3 3v-3H2z"/></svg>4</span></div>
</div>
<div class="shot" style="left:598px;top:2975px;width:238px;height:215px;background:linear-gradient(150deg,#2c2c2e,#b8b3a6 55%,#e2ddd2)" role="img" aria-label="Photo of a car masked up for spraying"></div>
<div class="shot" style="left:851px;top:2975px;width:235px;height:215px;background:linear-gradient(160deg,#9fa2a6,#5b5650 55%,#2d2b29)" role="img" aria-label="Photo of a bronze saloon car front"></div>
<div class="shot" style="left:112px;top:3207px;width:235px;height:213px;background:radial-gradient(circle,#3a3b3f,#0f1012)" role="img" aria-label="Photo of a black motorcycle"></div>
<div class="shot" style="left:364px;top:3207px;width:236px;height:213px;background:radial-gradient(circle,#3a4466,#12152a)" role="img" aria-label="Photo of a dark sports motorcycle"></div>
<div class="shot" style="left:615px;top:3207px;width:471px;height:213px;background:linear-gradient(120deg,#3b3f46,#c7c9cc 45%,#7a1a1e 70%,#23252a)" role="img" aria-label="Photo of a motorcycle rear suspension close up"></div>

<!-- partners -->
<div class="partner" style="left:108px">DORFLINT</div>
<div class="partner" style="left:308px">KEBO</div>
<div class="partner" style="left:508px">VASTINCO</div>
<div class="partner" style="left:708px">Q WRAP</div>
<div class="partner" style="left:908px">GLENBRUSH</div>

<!-- contact -->
<section class="abs contact-band"></section>
<h2 class="abs heading" style="left:112px;top:3721px;color:#fff">Contact us</h2>
<div class="abs c-item" style="top:3793px"><svg viewBox="0 0 24 24"><path fill="#fff" d="M12 2a7 7 0 00-7 7c0 5 7 13 7 13s7-8 7-13a7 7 0 00-7-7zm0 9.5A2.5 2.5 0 1112 6a2.5 2.5 0 010 5.5z"/></svg><span>Harrow Works Park,<br>Fern Lane, Oakby,<br>Westshire, WS12 7QP</span></div>
<div class="abs c-item" style="top:3891px"><svg viewBox="0 0 24 24"><path fill="#fff" d="M6.6 10.8a15 15 0 006.6 6.6l2.2-2.2c.3-.3.7-.4 1-.2 1.1.4 2.3.6 3.6.6.6 0 1 .4 1 1V20c0 .6-.4 1-1 1A17 17 0 013 4c0-.6.4-1 1-1h3.5c.6 0 1 .4 1 1 0 1.3.2 2.5.6 3.6.1.3 0 .7-.2 1z"/></svg><span>0770 900 1234</span></div>
<div class="abs c-item" style="top:3934px"><svg viewBox="0 0 24 24"><rect x="2" y="5" width="20" height="14" fill="none" stroke="#fff" stroke-width="2"/><path d="M2 5l10 8 10-8" stroke="#fff" stroke-width="2" fill="none"/></svg><span>sales@brenvashine.co.uk</span></div>
<div class="abs c-item" style="top:3981px"><svg viewBox="0 0 24 24"><circle cx="12" cy="12" r="9.5" fill="none" stroke="#fff" stroke-width="1.8"/><ellipse cx="12" cy="12" rx="4" ry="9.5" fill="none" stroke="#fff" stroke-width="1.6"/><path d="M2.5 12h19M4 7h16M4 17h16" stroke="#fff" stroke-width="1.4"/></svg><span>www.brenvashine.co.uk</span></div>

<footer class="abs footer"></footer>
<div class="abs f-label">RECENT POST</div>
<div class="post-thumb" style="left:110px" role="img" aria-label="Photo of a technician spraying a car"></div>
<div class="post" style="left:200px"><b>Ipsum dolor</b><br>By Admin / 💬 28<br><em>Read more</em></div>
<div class="post-thumb" style="left:337px" role="img" aria-label="Photo of a car in the paint booth"></div>
<div class="post" style="left:427px"><b>Ipsum dolor</b><br>By Admin / 💬 28<br><em>Read more</em></div>
<div class="social" style="left:110px">Kiv</div>
<div class="social" style="left:164px">Tru</div>
<div class="social" style="left:219px">Pho</div>
<div class="social" style="left:273px">Glo</div>
<div class="abs pay-label">Secured Payments By</div>
<div class="abs pay-name">TILLWAVE</div>
<div class="abs copy">© Copyright 2019 | Brenvashine</div>

<!-- appointment -->
<div class="abs appt">
  <h2 class="heading">Make an appoinment</h2>
  <p class="appt-addr">Brenvashine Bodyshop, Harrow Works Park, Fern Lane, Oakby, Westshire, WS12 7QP</p>
  <div class="field" style="top:166px">Name</div>
  <div class="field" style="top:229px">Time</div>
  <div class="field" style="top:292px">Price</div>
  <div class="field select" style="top:352px">Select Date</div>
  <div class="btn">Submit</div>
  <p class="appt-note">If you are unable to keep your appointment, Please contact us as soon as possible</p>
</div>

</body>
</html>
```